Velk Partners Building Business Cards

We need a business card that reflects our business as "Solar Experts" in San Diego. Browse our website www.velkpartners.example our License needs to be displayed as "CSLB# 3867140" our phone number is (619) 555-0187

Save thousands on your electric bills and increase the value of your home while helping to protect the environment. Our solar installation experts will help you design the system that's right for you, using only the highest quality equipment that will look great and give you ideal performance. Our goal is to make you energy independent, and get your electric bill to 0.

Paul Osterby
(619) 555-0187
paul@velkpartners.example

Target Market(s)

Home owners in san diego looking for solar

Industry/Entity Type

Solar Energy

Contact Information for Business Card

Paul Osterby
(619) 555-0187
paul@velkpartners.example

Font styles to use
Other font styles liked:
• Use our logo font

Requirements
Must have
• License needs to be displayed as "CSLB# 3867140" our phone number is (619) 555-0187
Nice to have
• Real images of rooftop home solar in san diego
Should not have
• our business address

```html
<!DOCTYPE html>
<html lang="en">
<head>
<meta charset="utf-8">
<title>Velk Partners Building — Business Cards</title>
<link rel="stylesheet" href="https://fonts.googleapis.com/css2?family=Open+Sans:wght@400;600;700&display=swap">
<style>
  :root {
    --backdrop: #ecebe8;
    --card-white: #ffffff;
    --card-yellow: #f8ad04;
    --brand-navy: #1d3f7e;
    --accent-orange: #f3a712;
    --ink: #222222;
    --card-shadow: 0 6px 18px rgba(0, 0, 0, 0.18);
  }
  * { box-sizing: border-box; margin: 0; padding: 0; }
  html, body {
    width: 1200px;
    height: 900px;
    overflow: hidden;
    background: var(--backdrop);
    font-family: "Open Sans", Arial, sans-serif;
  }
  .canvas { position: relative; width: 1200px; height: 900px; }

  .card {
    position: absolute;
    box-shadow: var(--card-shadow);
    display: flex;
    flex-direction: column;
    align-items: center;
  }
  .card--front {
    left: 78px; top: 35px;
    width: 587px; height: 362px;
    background: var(--card-white);
  }
  .card--back {
    left: 388px; top: 505px;
    width: 567px; height: 352px;
    background: var(--card-yellow);
    justify-content: center;
  }

  .wordmark {
    font-weight: 700;
    text-align: center;
    letter-spacing: -0.5px;
    line-height: 1.05;
  }
  .card--front .wordmark {
    margin-top: 62px;
    font-size: 40px;
    color: var(--brand-navy);
  }
  .card--back .wordmark {
    margin-top: 8px;
    font-size: 38px;
    color: var(--card-white);
  }

  .holder-name {
    margin-top: 42px;
    font-size: 18px;
    font-weight: 600;
    color: var(--accent-orange);
    letter-spacing: 0.3px;
  }
  .contact-list {
    list-style: none;
    margin-top: 12px;
    text-align: center;
    font-size: 15px;
    color: var(--ink);
    line-height: 22px;
  }
  .contact-list li {
    display: flex;
    align-items: center;
    justify-content: center;
    gap: 6px;
  }
  .contact-icon { width: 11px; height: 11px; fill: var(--accent-orange); }
  .license {
    margin-top: 22px;
    font-size: 15px;
    color: var(--ink);
  }
  .license-label { color: var(--accent-orange); font-weight: 600; }
</style>
</head>
<body>
<main class="canvas">

  <section class="card card--front" aria-label="Business card front">
    <h1 class="wordmark">Velk Partners Building Inc</h1>
    <p class="holder-name">PAUL OSTERBY</p>
    <ul class="contact-list">
      <li>
        <svg class="contact-icon" viewBox="0 0 24 24" aria-hidden="true">
          <path d="M6.6 10.8a15.1 15.1 0 0 0 6.6 6.6l2.2-2.2c.3-.3.7-.4 1-.2 1.1.4 2.3.6 3.6.6.6 0 1 .4 1 1V20c0 .6-.4 1-1 1A17 17 0 0 1 3 4c0-.6.4-1 1-1h3.5c.6 0 1 .4 1 1 0 1.3.2 2.5.6 3.6.1.3 0 .7-.2 1z"/>
        </svg>
        (619) 555-0187
      </li>
      <li>
        <svg class="contact-icon" viewBox="0 0 24 24" aria-hidden="true">
          <path d="M2 5h20v14H2z M2 5l10 8 10-8" />
        </svg>
        paul@velkpartners.example
      </li>
    </ul>
    <p class="license"><span class="license-label">LICENSE:</span> CSLB# 3867140</p>
  </section>

  <section class="card card--back" aria-label="Business card back">
    <h2 class="wordmark">Velk Partners Building Inc</h2>
  </section>

</main>
</body>
</html>
```